Business Card for a Jewellery Brand

Business card for an upscale jewellery brand. Attached is the brand logo and icon and color board. I am looking for two card versions: one for the founder and one is generic. The card should be elegant and convey upscale and premium feel. I am open to both square and rectangle card shapes.

Industry/Entity Type

Jewelry

Contact Information for Business Card

Two cards: (1) Sunela Parvaniya (Founder) (2) General
(1) Sunela Parvaniya card should have Name: Sunela Parvaniya, Title: Founder Email id: sunela@quiremo.com.au. Phone no: +61452913307
(2) Generic card should have Email id: info@quiremo.com.au. Phone no: +61436207518

Requirements
Must have
• Workmark
• ICON
• Phone no
• Email ID
• ABN: 58219740312 (Note: ABN is Business number in Australia)
• Website: www.quiremo.com.au
• Instagram: quiremo_jewellery
• Facebook: @quiremojewellery
Nice to have
• Tagline

```html
<!DOCTYPE html>
<html lang="en">
<head>
<meta charset="utf-8">
<title>Quiremo Business Card</title>
<link rel="stylesheet" href="https://fonts.googleapis.com/css2?family=Roboto:wght@300;400&family=Roboto+Condensed:wght@700&display=swap">
<style>
  :root {
    --backdrop: #2a2a2a;
    --card-white: #fbfbfa;
    --blush: #e69a95;
    --blush-text: #e3908c;
    --ink: #454545;
    --muted: #8a8a8a;
    --rule: #9a9a9a;
    --white: #ffffff;
  }
  * { margin: 0; padding: 0; box-sizing: border-box; }
  html, body { width: 1200px; height: 960px; overflow: hidden; }
  body {
    position: relative;
    background: var(--backdrop);
    font-family: "Roboto", Arial, sans-serif;
  }
  .card {
    position: absolute;
    width: 600px;
    height: 342px;
  }
  .card-front { left: 302px; top: 129px; background: var(--card-white); }
  .card-back { left: 299px; top: 488px; background: var(--blush); }

  .brand-mark {
    position: absolute;
    right: 25px;
    top: 24px;
    width: 180px;
    text-align: right;
  }
  .brand-dot {
    display: block;
    width: 62px;
    height: 62px;
    margin: 6px 32px 0 auto;
    border: 3px solid var(--blush);
    border-radius: 50%;
  }
  .brand-name {
    display: block;
    margin-top: 34px;
    font-weight: 400;
    font-size: 31px;
    line-height: 34px;
    letter-spacing: 7px;
    margin-right: -7px;
    color: var(--blush);
  }

  .holder-name {
    position: absolute;
    left: 24px;
    top: 192px;
    font-family: "Roboto Condensed", Arial, sans-serif;
    font-weight: 700;
    font-size: 21px;
    color: var(--blush-text);
  }
  .holder-title {
    position: absolute;
    left: 24px;
    top: 219px;
    width: 548px;
    display: flex;
    align-items: center;
    font-size: 15px;
    color: var(--muted);
  }
  .holder-title::after {
    content: "";
    flex: 1;
    height: 1px;
    margin-top: 3px;
    background: var(--rule);
  }

  .contact-list {
    position: absolute;
    left: 25px;
    top: 246px;
    list-style: none;
    font-size: 14px;
    line-height: 18px;
    color: var(--ink);
  }
  .contact-list li { display: flex; align-items: center; }
  .contact-icon { width: 14px; height: 14px; margin-right: 8px; flex: none; }

  .business-details {
    position: absolute;
    right: 25px;
    top: 283px;
    text-align: right;
    font-size: 14px;
    line-height: 18px;
    color: var(--ink);
  }

  .back-mark {
    position: absolute;
    left: 0;
    right: 0;
    top: 92px;
    text-align: center;
    color: var(--white);
  }
  .back-dot {
    display: block;
    width: 92px;
    height: 92px;
    margin: 0 auto;
    border: 8px solid var(--white);
    border-radius: 50%;
  }
  .back-name {
    display: block;
    margin-top: 30px;
    font-weight: 400;
    font-size: 40px;
    letter-spacing: 10px;
    margin-right: -10px;
  }

  .tagline {
    position: absolute;
    left: 84px;
    top: 297px;
    width: 410px;
    display: flex;
    align-items: center;
    font-size: 14px;
    color: var(--white);
    white-space: nowrap;
  }
  .tagline::before,
  .tagline::after {
    content: "";
    flex: 1;
    height: 2px;
  }
  .tagline::before {
    margin-right: 4px;
    background: linear-gradient(to right, rgba(255,255,255,0), var(--white));
  }
  .tagline::after {
    margin-left: 4px;
    background: linear-gradient(to left, rgba(255,255,255,0), var(--white));
  }
</style>
</head>
<body>
  <section class="card card-front">
    <div class="brand-mark">
      <span class="brand-dot"></span>
      <span class="brand-name">QUIREMO</span>
    </div>

    <h1 class="holder-name">Sunela Parvaniya</h1>
    <p class="holder-title">Founder</p>

    <ul class="contact-list">
      <li>
        <svg class="contact-icon" viewBox="0 0 14 14" aria-hidden="true">
          <rect x="3.5" y="1" width="7" height="12" rx="1.2" fill="none" stroke="var(--blush)" stroke-width="1.5"/>
          <line x1="6" y1="11" x2="8" y2="11" stroke="var(--blush)" stroke-width="1"/>
        </svg>
        +61452913307
      </li>
      <li>
        <svg class="contact-icon" viewBox="0 0 14 14" aria-hidden="true">
          <rect x="1" y="3" width="12" height="8.5" fill="var(--blush)"/>
          <polyline points="1,3 7,8 13,3" fill="none" stroke="var(--card-white)" stroke-width="1.2"/>
        </svg>
        sunela@quiremo.com.au
      </li>
      <li>
        <svg class="contact-icon" viewBox="0 0 14 14" aria-hidden="true">
          <rect x="2" y="2" width="10" height="10" rx="1.5" fill="var(--blush)"/>
        </svg>
        quiremo_jewellery
      </li>
      <li>
        <svg class="contact-icon" viewBox="0 0 14 14" aria-hidden="true">
          <rect x="2" y="2" width="10" height="10" rx="1.5" fill="var(--blush)"/>
        </svg>
        @quiremojewellery
      </li>
    </ul>

    <div class="business-details">
      <p>ABN: 58219740312</p>
      <p>www.quiremo.com.au</p>
    </div>
  </section>

  <section class="card card-back">
    <div class="back-mark">
      <span class="back-dot"></span>
      <span class="back-name">QUIREMO</span>
    </div>
    <p class="tagline">LOVE IS IN THE AIR</p>
  </section>
</body>
</html>
```